I need a sophisticated and powerful book cover design that combines Japanese minimalism with contemporary appeal. The cover should convey personal transformation through the metaphor of a katana (Japanese sword).
Key Design Elements:
A katana, either partially shown or artistically rendered
Subtle Japanese design elements without being stereotypical
Clean, minimalist aesthetic
Professional font selection that bridges Eastern and Western typography
Color scheme: Deep blacks, steel grays, and possibly a touch of red or gold for accent
Mood/Style:
Professional and sophisticated
Blend of traditional Japanese aesthetics with modern design
Should appeal to personal development and business readers
Must convey strength and transformation
Elegant rather than aggressive
Specific Requirements:
Title: "The Lantern Compass"
Subtitle: "Quiet Methods for Growing Inner Steadiness and Calm Endurance"
Author names: Dorvelan Thaske and Meloda Thaske
Cover dimensions: Standard hardcover book size (6" x 9")
Must work well in both physical and digital thumbnail formats
Should be striking and legible when viewed as a small image online
Design Specifics:
Japanese elements such as brushstroke effects, kanji characters, or wave patterns
The design should reflect the book's core message: personal transformation through Japanese wisdom principles, using the katana as a metaphor for growth and development.

```html
<!DOCTYPE html>
<html lang="en">
<head>
<meta charset="utf-8">
<title>The Lantern Compass — Book Cover</title>
<link rel="stylesheet" href="https://fonts.googleapis.com/css2?family=Cinzel:wght@400;600;700&display=swap">
<style>
  :root {
    --page: #ffffff;
    --ink: #000000;
    --paper: #ffffff;
    --accent: #ed1c24;
    --sun-top: #6f0f1c;
    --sun-mid: #c0232a;
    --sun-low: #f3c6c8;
    --sun-base: #ffffff;
  }
  html, body {
    margin: 0;
    padding: 0;
    width: 1200px;
    height: 1200px;
    overflow: hidden;
    background: var(--page);
  }
  .cover {
    position: absolute;
    left: 235px;
    top: 52px;
    width: 730px;
    height: 1096px;
    background: var(--ink);
    font-family: "Cinzel", "Trajan Pro", serif;
    text-align: center;
    overflow: hidden;
  }
  .title {
    margin: 0;
    position: absolute;
    left: 0;
    right: 0;
    top: 40px;
    font-weight: 400;
    line-height: 1;
  }
  .title-line {
    display: block;
    white-space: nowrap;
  }
  .title-lead {
    color: var(--paper);
    font-size: 96px;
    letter-spacing: 1px;
  }
  .title-key {
    color: var(--accent);
    font-size: 124px;
    margin-top: 22px;
    letter-spacing: 1px;
  }
  .subtitle {
    position: absolute;
    left: 45px;
    right: 45px;
    top: 334px;
    margin: 0;
    color: var(--paper);
    font-size: 28px;
    font-weight: 600;
    line-height: 48px;
    letter-spacing: 1.5px;
  }
  .art {
    position: absolute;
    left: 0;
    top: 429px;
    width: 730px;
    height: 540px;
  }
  .author-band {
    position: absolute;
    left: 0;
    right: 0;
    bottom: 0;
    height: 95px;
    background: var(--accent);
    display: flex;
    align-items: center;
    justify-content: center;
    padding: 0 40px;
    box-sizing: border-box;
  }
  .authors {
    margin: 0;
    color: var(--paper);
    font-size: 27px;
    font-weight: 400;
    letter-spacing: 1px;
    white-space: nowrap;
  }
</style>
</head>
<body>
  <main class="cover">
    <h1 class="title">
      <span class="title-line title-lead">The Lantern</span>
      <span class="title-line title-key">COMPASS</span>
    </h1>
    <p class="subtitle">Quiet Methods for Growing Inner Steadiness and Calm Endurance</p>

    <svg class="art" viewBox="0 0 730 540" role="img"
         aria-label="Two katanas resting on a black lacquered stand in front of a large red rising sun">
      <defs>
        <linearGradient id="sun-fade" x1="0" y1="0" x2="0" y2="1">
          <stop offset="0" stop-color="var(--sun-top)"/>
          <stop offset="0.55" stop-color="var(--sun-mid)"/>
          <stop offset="0.82" stop-color="var(--sun-low)"/>
          <stop offset="1" stop-color="var(--sun-base)"/>
        </linearGradient>
      </defs>
      <circle cx="349" cy="273" r="232" fill="url(#sun-fade)"/>
    </svg>

    <footer class="author-band">
      <p class="authors">Dorvelan Thaske and Meloda Thaske</p>
    </footer>
  </main>
</body>
</html>
```